Local Flower Farm Needs Business Card Design

I need business cards designed for a flower farm based in Eudora, Kansas.
Business Info:
We are a local cut flower farm located in Eudora, Kansas, founded by Corinne Haldwick. What started as a passion for agriculture and search for more joy in daily life has blossomed into a small business dedicated to providing the community with beautiful, fresh, and sustainable flowers. We specialize in local, seasonal blooms, ensuring that every petal reflects the care and dedication we pour into our craft. Our mission is to deliver the highest quality flowers directly to our customers through local farmers markets and to florists who share our commitment to sustainability. Join us in celebrating the beauty of nature, one bloom at a time!
Contact Details:
Corinne Haldwick
Owner
Phone 913-555-0147
Facebook: Rosalind Thorpe Gardens
Instagram: @RosalindThorpeGardens
Website: RosalindThorpeGardens.example
Target Market(s)
Wholesale to Florists and Direct to Consumer via Farmers Market
Industry/Entity Type
Florist, Farm
Contact Information for Business Card
Name, Contact Info, Logo
Look and feel
Each slider illustrates characteristics of the customer's brand and the style your logo design should communicate.

```html
<!DOCTYPE html>
<html lang="en">
<head>
<meta charset="utf-8">
<title>Rosalind Thorpe Gardens – Business Cards</title>
<link rel="stylesheet" href="https://fonts.googleapis.com/css2?family=Tinos:wght@400;700&display=swap">
<style>
  :root {
    --backdrop: #16181a;
    --card-deep: #08191c;
    --card-mid: #0d2a2f;
    --sheen-strong: rgba(58, 122, 130, 0.55);
    --sheen-soft: rgba(38, 92, 100, 0.35);
    --ink: #ffffff;
    --ink-soft: rgba(255, 255, 255, 0.85);
  }
  * { box-sizing: border-box; margin: 0; padding: 0; }
  html, body { width: 1200px; height: 840px; overflow: hidden; }
  body {
    background: var(--backdrop);
    font-family: "Tinos", "Times New Roman", serif;
    color: var(--ink);
    position: relative;
  }
  .card {
    position: absolute;
    width: 560px;
    height: 330px;
    border-radius: 26px;
    overflow: hidden;
    background: linear-gradient(160deg, var(--card-mid) 0%, var(--card-deep) 55%, var(--card-mid) 100%);
    box-shadow: 0 18px 40px rgba(0, 0, 0, 0.55);
  }
  .card--front { left: 60px; top: 70px; }
  .card--back { left: 580px; top: 440px; }

  .monogram-decoration {
    position: absolute;
    inset: 0;
    background:
      radial-gradient(ellipse 150px 190px at 80% 55%, var(--sheen-strong) 0%, transparent 100%),
      radial-gradient(ellipse 230px 260px at 72% 40%, var(--sheen-soft) 0%, transparent 100%);
  }

  .brand {
    position: absolute;
    display: flex;
    align-items: center;
    gap: 14px;
  }
  .brand__dot {
    flex: none;
    border: 2px solid var(--ink);
    border-radius: 50%;
  }
  .brand__name {
    font-weight: 400;
    color: var(--ink);
    letter-spacing: 0.06em;
    text-transform: uppercase;
    line-height: 1.15;
  }
  .card--front .brand { left: 48px; top: 118px; }
  .card--front .brand__dot { width: 34px; height: 34px; }
  .card--front .brand__name { font-size: 26px; width: 190px; }

  .card--back .brand { left: 40px; top: 48px; }
  .card--back .brand__dot { width: 22px; height: 22px; }
  .card--back .brand__name { font-size: 17px; width: 140px; }

  .person {
    position: absolute;
    left: 40px;
    top: 190px;
  }
  .person__name {
    font-weight: 700;
    font-size: 25px;
    letter-spacing: 0.03em;
    text-transform: uppercase;
  }
  .person__role { font-size: 17px; color: var(--ink-soft); }

  .contacts {
    position: absolute;
    left: 40px;
    top: 258px;
    display: grid;
    grid-template-columns: auto auto;
    column-gap: 22px;
    row-gap: 8px;
    font-size: 15px;
  }
  .contact { display: flex; align-items: center; gap: 7px; white-space: nowrap; }
  .contact__icon { width: 14px; height: 14px; flex: none; }
  .contact__square { width: 12px; height: 12px; background: var(--ink); border-radius: 2px; flex: none; }
  .contact__circle { width: 13px; height: 13px; background: var(--ink); border-radius: 50%; flex: none; }
</style>
</head>
<body>

  <section class="card card--front" aria-label="Business card front">
    <div class="monogram-decoration" role="img" aria-label="Faint large brand monogram with line-drawn flowers"></div>
    <div class="brand">
      <span class="brand__dot"></span>
      <span class="brand__name">Rosalind Thorpe Gardens</span>
    </div>
  </section>

  <section class="card card--back" aria-label="Business card back">
    <div class="monogram-decoration" role="img" aria-label="Faint large brand monogram with line-drawn flowers"></div>
    <div class="brand">
      <span class="brand__dot"></span>
      <span class="brand__name">Rosalind Thorpe Gardens</span>
    </div>

    <div class="person">
      <p class="person__name">Corinne Haldwick</p>
      <p class="person__role">Owner</p>
    </div>

    <div class="contacts">
      <p class="contact">
        <svg class="contact__icon" viewBox="0 0 24 24" aria-hidden="true">
          <path fill="#fff" d="M6.6 10.8a15.1 15.1 0 0 0 6.6 6.6l2.2-2.2a1 1 0 0 1 1-.25 11.4 11.4 0 0 0 3.6.57 1 1 0 0 1 1 1V20a1 1 0 0 1-1 1A17 17 0 0 1 3 4a1 1 0 0 1 1-1h3.5a1 1 0 0 1 1 1c0 1.25.2 2.45.57 3.57a1 1 0 0 1-.25 1z"/>
        </svg>
        913-555-0147
      </p>
      <p class="contact"><span class="contact__square"></span>Rosalind Thorpe Gardens</p>
      <p class="contact"><span class="contact__square"></span>@RosalindThorpeGardens</p>
      <p class="contact"><span class="contact__circle"></span>RosalindThorpeGardens.example</p>
    </div>
  </section>

</body>
</html>
```